Business Card Design

We need a business card designed for our new company. Prefer a black card with white logo & writing.

Contact Information for Business Card

Ted Galloway, address: 7-4812 Fernhollow Road, Abbotsford, BC, V3K 8R2, Office Phone: 604-712-3390, Cell: 604-947-2164, Email: ted@resinworkshub.ca

Colors

Designer to choose only greyscale colors for use in the design.

```html
<!DOCTYPE html>
<html lang="en">
<head>
<meta charset="utf-8">
<title>Resin Works Hub — Business Card</title>
<link rel="stylesheet" href="https://fonts.googleapis.com/css2?family=Montserrat:wght@300;600;800&display=swap">
<style>
  :root {
    --page: #d9d9d9;
    --card: #141414;
    --ink: #ffffff;
    --ink-soft: #e6e6e6;
    --disc: #ffffff;
  }
  * { box-sizing: border-box; margin: 0; padding: 0; }
  html, body { width: 1200px; height: 716px; overflow: hidden; }
  body {
    background: var(--page);
    font-family: "Montserrat", sans-serif;
    color: var(--ink);
    position: relative;
  }
  .card {
    position: absolute;
    top: 203px;
    width: 540px;
    height: 310px;
    background: var(--card);
    overflow: hidden;
    box-shadow: 0 6px 18px rgba(0,0,0,0.25);
  }
  .card--back { left: 52px; }
  .card--front { left: 608px; }

  .disc {
    position: absolute;
    top: 40px;
    width: 230px;
    height: 230px;
    border-radius: 50%;
    background: var(--disc);
  }
  .card--back .disc { left: 425px; }
  .card--front .disc { left: -115px; }

  .wordmark {
    font-weight: 800;
    text-transform: uppercase;
    line-height: 1.05;
    color: var(--ink);
    letter-spacing: 0.02em;
  }
  .card--back .wordmark {
    position: absolute;
    left: 36px;
    top: 30px;
    font-size: 17px;
  }
  .card--front .wordmark {
    position: absolute;
    right: 40px;
    bottom: 42px;
    font-size: 34px;
    text-align: right;
  }

  .contact {
    position: absolute;
    left: 36px;
    top: 104px;
  }
  .contact__name {
    font-weight: 600;
    font-size: 19px;
    margin-bottom: 12px;
  }
  .contact__address,
  .contact__line {
    font-weight: 300;
    font-size: 12.5px;
    line-height: 1.55;
    color: var(--ink-soft);
  }
  .contact__address { margin-bottom: 6px; }
  .contact__line { display: flex; align-items: center; gap: 7px; }
  .contact__icon { width: 11px; height: 11px; flex: none; }
</style>
</head>
<body>

  <section class="card card--back" aria-label="Business card, contact side">
    <div class="wordmark">Resin Works<br>Hub</div>

    <div class="contact">
      <p class="contact__name">Ted Galloway</p>
      <p class="contact__address">7-4812 Fernhollow Road,<br>Abbotsford, BC, V3K 8R2</p>
      <p class="contact__line">
        <svg class="contact__icon" viewBox="0 0 12 12" aria-hidden="true"><path d="M2.5 1h2l1 3-1.3 1a6 6 0 0 0 2.8 2.8l1-1.3 3 1v2a1 1 0 0 1-1 1A9.5 9.5 0 0 1 1.5 2a1 1 0 0 1 1-1z" fill="#fff"/></svg>
        604-712-3390
      </p>
      <p class="contact__line">
        <svg class="contact__icon" viewBox="0 0 12 12" aria-hidden="true"><rect x="3" y="0.8" width="6" height="10.4" rx="1" fill="none" stroke="#fff" stroke-width="1"/><circle cx="6" cy="9.4" r="0.6" fill="#fff"/></svg>
        604-947-2164
      </p>
      <p class="contact__line">
        <svg class="contact__icon" viewBox="0 0 12 12" aria-hidden="true"><rect x="0.8" y="2.3" width="10.4" height="7.4" rx="1" fill="none" stroke="#fff" stroke-width="1"/><path d="M1 2.8 6 6.6l5-3.8" fill="none" stroke="#fff" stroke-width="1"/></svg>
        ted@resinworkshub.ca
      </p>
    </div>

    <div class="disc" aria-hidden="true"></div>
  </section>

  <section class="card card--front" aria-label="Business card, brand side">
    <div class="disc" aria-hidden="true"></div>
    <div class="wordmark">Resin Works<br>Hub</div>
  </section>

</body>
</html>
```